Whitcombe Business Card Design

The name of the business is Dario Whitcombe, CPA LLC
The service that we offer is Accounting, Tax & Consulting Services. I need it to have the following items:
Dario Whitcombe, Principal
Phone Number
Email Address
Physical Address

I have attached the company logo, one in black and one in white. Please provide a design in black background and the other in white background. Please include "Accounting, Tax & Consulting Services". I want the business card to be clean and very professional.

```html
<!DOCTYPE html>
<html lang="en">
<head>
<meta charset="UTF-8">
<title>Dario Whitcombe, CPA LLC — Business Cards</title>
<link rel="stylesheet" href="https://fonts.googleapis.com/css2?family=Montserrat:wght@500;600&family=Rajdhani:wght@600;700&family=Roboto:wght@400;500&display=swap">
<style>
  :root {
    --backdrop: #d6d6d4;
    --card-light: #f6f6f4;
    --card-dark: #232323;
    --ink: #2f2f31;
    --ink-soft: #8a8a8c;
    --accent: #9b1b1e;
    --white: #ffffff;
  }
  * { margin: 0; padding: 0; box-sizing: border-box; }
  html, body { width: 1200px; height: 874px; overflow: hidden; background: var(--backdrop); }
  .canvas { position: relative; width: 1200px; height: 874px; }

  .card {
    position: absolute;
    left: 290px;
    width: 620px;
    height: 354px;
    box-shadow: 0 6px 18px rgba(0,0,0,0.18);
  }

  /* Front card */
  .card--front {
    top: 64px;
    background: var(--card-light);
    display: flex;
    flex-direction: column;
    align-items: center;
    justify-content: center;
    text-align: center;
  }
  .brand {
    display: flex;
    align-items: center;
    gap: 12px;
  }
  .brand__square {
    width: 18px; height: 18px;
    background: var(--accent);
  }
  .brand__name {
    font-family: "Montserrat", sans-serif;
    font-weight: 600;
    font-size: 29px;
    letter-spacing: 1px;
    text-transform: uppercase;
    color: var(--ink);
  }
  .front__title {
    margin-top: 6px;
    font-family: "Montserrat", sans-serif;
    font-weight: 500;
    font-size: 19px;
    letter-spacing: 4px;
    text-transform: uppercase;
    color: var(--ink-soft);
  }
  .front__services {
    margin-top: 40px;
    font-family: "Rajdhani", sans-serif;
    font-weight: 700;
    font-size: 18px;
    letter-spacing: 0.5px;
    text-transform: uppercase;
    color: var(--accent);
  }
  .front__services span { color: var(--ink); font-weight: 600; }

  /* Back card */
  .card--back {
    top: 458px;
    background: var(--card-dark);
  }
  .back__frame {
    position: absolute;
    inset: 20px;
    border: 1px solid var(--accent);
  }
  .back__brand {
    position: absolute;
    left: 44px; top: 44px;
    display: flex; align-items: center; gap: 10px;
  }
  .back__brand .brand__square { width: 14px; height: 14px; }
  .back__brand .brand__name { font-size: 17px; color: var(--white); }

  .contact {
    position: absolute;
    left: 392px;
    top: 306px;
    width: 270px;
    transform: rotate(-90deg);
    transform-origin: top left;
    font-family: "Roboto", sans-serif;
    color: var(--white);
  }
  .contact__name {
    font-family: "Rajdhani", sans-serif;
    font-weight: 700;
    font-size: 28px;
    line-height: 28px;
    text-transform: uppercase;
    color: var(--accent);
  }
  .contact__role {
    font-size: 14px;
    letter-spacing: 1px;
    text-transform: uppercase;
    margin-bottom: 8px;
  }
  .contact__line {
    display: flex;
    align-items: center;
    gap: 8px;
    font-size: 14.5px;
    line-height: 21px;
  }
  .contact__icon { width: 11px; height: 11px; flex: none; }
  .contact__line--plain { padding-left: 19px; }

  .back__bar {
    position: absolute;
    left: 384px;
    top: 318px;
    width: 178px;
    height: 9px;
    background: var(--white);
  }
</style>
</head>
<body>
<div class="canvas">

  <section class="card card--front">
    <div class="brand">
      <div class="brand__square"></div>
      <div class="brand__name">Dario Whitcombe, CPA, LLC</div>
    </div>
    <div class="front__title">Certified Public Accountant</div>
    <div class="front__services">Accounting, Tax &amp; Consulting <span>Services</span></div>
  </section>

  <section class="card card--back">
    <div class="back__frame"></div>
    <div class="back__brand">
      <div class="brand__square"></div>
      <div class="brand__name">Dario Whitcombe</div>
    </div>

    <div class="contact">
      <div class="contact__name">Dario Whitcombe</div>
      <div class="contact__role">Principal</div>
      <div class="contact__line">
        <svg class="contact__icon" viewBox="0 0 12 12" aria-hidden="true"><path d="M6 0.5a4 4 0 0 0-4 4c0 3 4 7 4 7s4-4 4-7a4 4 0 0 0-4-4zm0 5.5a1.5 1.5 0 1 1 0-3 1.5 1.5 0 0 1 0 3z" fill="#9b1b1e"/></svg>
        <span>4120 Juniper Court</span>
      </div>
      <div class="contact__line contact__line--plain">Fairview, Alaska 99517</div>
      <div class="contact__line">
        <svg class="contact__icon" viewBox="0 0 12 12" aria-hidden="true"><path d="M2.5 1l2 0 1 2.8-1.3 1a6 6 0 0 0 2.9 2.9l1-1.3 2.8 1 0 2a1 1 0 0 1-1 1A10 10 0 0 1 1.5 2a1 1 0 0 1 1-1z" fill="#9b1b1e"/></svg>
        <span>555-204-7731</span>
      </div>
      <div class="contact__line">
        <svg class="contact__icon" viewBox="0 0 12 12" aria-hidden="true"><rect x="0.5" y="2" width="11" height="8" rx="1" fill="#9b1b1e"/><path d="M1 2.7l5 3.6 5-3.6" stroke="#232323" stroke-width="1" fill="none"/></svg>
        <span>dario@dariowhitcombecpa.com</span>
      </div>
      <div class="contact__line">
        <svg class="contact__icon" viewBox="0 0 12 12" aria-hidden="true"><circle cx="6" cy="6" r="5.5" fill="#9b1b1e"/><path d="M0.8 6h10.4M6 0.6c-2.2 2.8-2.2 8 0 10.8M6 0.6c2.2 2.8 2.2 8 0 10.8" stroke="#232323" stroke-width="0.8" fill="none"/></svg>
        <span>www.dariowhitcombecpa.com</span>
      </div>
    </div>

    <div class="back__bar"></div>
  </section>

</div>
</body>
</html>
```